Clinic for cellulit and fat removal

Name of clinic :
Lirava
- Body & Health (this has to be written on the site.)
I need CMS for me to be able to make changes myself.
A webpage for woman searching for a solution to remove fat and cellulit.
The owner is a brazilian woman in Denmark, and want her sense of aestetic shines thru the website.
There needs to be a slide show on the landing page showing big sliding pictures, of the clinic and and the treatments.
The Cryolipolysis, is a treatment freezing fat and cellulit, and this treatment will be the Attraction of the clinic.
Needs These pages in a horisontal fasion. (written in Danish)
Lirava
Behandlinger
- Cryolipolysis
- Trimflox
- Lymfemassage
- Korathelix
- Amberline Tide
Produkter
Priser
Kontakt
Clinic
Coded - Design and coding required
5+ page

```html
<!DOCTYPE html>
<html lang="da">
<head>
<meta charset="utf-8">
<title>Lirava – Body &amp; Health</title>
<link rel="stylesheet" href="https://fonts.googleapis.com/css2?family=Open+Sans:wght@400;600;700&display=swap">
<style>
:root{
  --teal:#2bbcd6;
  --lime:#b3c934;
  --orange:#f28c1a;
  --ink:#333;
  --body:#666;
  --muted:#999;
  --band:#eceff1;
  --line:#e2e5e8;
  --white:#fff;
}
*{box-sizing:border-box;margin:0;padding:0}
html,body{width:1200px;height:2560px;overflow:hidden}
body{position:relative;background:var(--white);font-family:"Open Sans",Arial,sans-serif;color:var(--body)}
.abs{position:absolute}

/* header */
.logo{left:131px;top:26px;font-size:46px;font-weight:700;color:var(--teal);letter-spacing:-1px;line-height:1}
.nav{top:44px;font-size:13.5px;color:var(--ink);transform:translateX(-50%)}
.nav.active{color:var(--orange)}
.lang{left:971px;top:36px;width:96px;height:35px;border:1px solid #ccc;border-radius:2px;font-size:11px;color:var(--muted);display:flex;align-items:center;padding-left:10px;gap:5px}
.lang .chev{position:absolute;right:8px;top:12px}

/* hero */
.hero{left:0;top:108px;width:1200px;height:506px;background:linear-gradient(100deg,#e9e3de 0%,#d9b59c 30%,#f3f2f0 55%,#eceef2 75%,#9a86c9 88%,#e6e8ec 100%)}
.hero-title{left:0;top:178px;width:1200px;text-align:center;font-size:50px;font-weight:700;color:#555;letter-spacing:1px}
.hero-arrow{top:346px;width:28px;height:28px;border-radius:50%;background:rgba(120,120,120,.75)}

/* welcome */
.welcome{left:0;top:683px;width:1200px;text-align:center;font-size:34px;font-weight:700;color:var(--lime)}
.lead{left:131px;top:736px;width:936px;text-align:center;font-size:16.5px;color:var(--ink)}
.intro{left:131px;top:767px;width:936px;text-align:justify;text-align-last:center;font-size:10.5px;line-height:18px;color:var(--muted)}

/* treatment cards */
.card{width:299px}
.card .photo{width:299px;height:297px}
.card .pill{position:absolute;left:21px;width:258px;height:45px;border-radius:23px;background:var(--orange);color:var(--white);font-weight:700;font-size:22px;display:flex;align-items:center;justify-content:center;top:274px}
.card .text{position:absolute;top:335px;left:20px;width:259px;text-align:justify;text-align-last:center;font-size:10.8px;line-height:17px;color:var(--muted)}
.card .more{position:absolute;top:390px;left:0;width:299px;text-align:center;font-size:10px;color:var(--orange);text-decoration:underline}

/* testimonials */
.band{left:0;top:1886px;width:1200px;height:572px;background:var(--band)}
.tcard{left:131px;top:1808px;width:936px;height:336px;background:var(--white);box-shadow:0 2px 8px rgba(0,0,0,.08)}
.ttitle{left:0;top:1844px;width:1200px;text-align:center;font-size:34px;font-weight:700;color:var(--lime)}
.avatar{top:1904px;width:80px;height:80px;border-radius:50%;border:3px solid #e4e4e4;background:linear-gradient(160deg,#d5d5d5,#8f8f8f)}
.avatar.dark{background:linear-gradient(160deg,#777,#333)}
.quote{left:251px;top:2005px;width:701px;text-align:center;font-size:12.5px;line-height:21px;color:var(--body)}
.qmark{top:2006px;font-size:64px;font-weight:700;color:#c8c8c8;line-height:1;font-family:Georgia,serif}
.author{left:0;top:2080px;width:1200px;text-align:center;font-size:12.5px;color:var(--ink);font-weight:600}

/* contact */
.ctitle{left:0;top:2190px;width:1200px;text-align:center;font-size:34px;font-weight:700;color:var(--teal)}
.field{height:41px;background:var(--white);border:1px solid var(--line);font-size:12px;color:#777;display:flex;align-items:center;padding-left:14px}
.submit{left:563px;top:2361px;width:74px;height:39px;background:var(--teal);color:var(--white);font-size:11px;display:flex;align-items:center;justify-content:center}

/* footer */
.flinks{left:131px;top:2488px;font-size:11px;color:var(--muted);word-spacing:4px}
.copy{left:131px;top:2513px;font-size:11px;color:var(--muted)}
.social{top:2495px;width:26px;height:26px;border-radius:50%}
</style>
</head>
<body>

<header>
  <div class="abs logo">LIRAVA</div>
  <span class="abs nav active" style="left:592px">Lirava</span>
  <span class="abs nav" style="left:700px">Behandlinger</span>
  <span class="abs nav" style="left:775px">Produkter</span>
  <span class="abs nav" style="left:850px">Priser</span>
  <span class="abs nav" style="left:920px">Kontakt</span>
  <div class="abs lang">
    <svg width="12" height="12" viewBox="0 0 12 12"><circle cx="6" cy="6" r="5" fill="#999"/><path d="M1 6h10M6 1c-2 2-2 8 0 10M6 1c2 2 2 8 0 10" stroke="#fff" stroke-width=".8" fill="none"/></svg>
    English
    <svg class="chev" width="9" height="9" viewBox="0 0 9 9"><path d="M1 3l3.5 3.5L8 3" stroke="#999" fill="none"/></svg>
  </div>
</header>

<section>
  <div class="abs hero" role="img" aria-label="Slideshow photo: a client relaxing on a treatment bed while a therapist applies a cryolipolysis device"></div>
  <h1 class="abs hero-title">BODY &amp; HEALTH</h1>
  <svg class="abs hero-arrow" style="left:22px" viewBox="0 0 28 28"><path d="M16 8l-6 6 6 6" stroke="#fff" stroke-width="3" fill="none"/></svg>
  <svg class="abs hero-arrow" style="left:1147px" viewBox="0 0 28 28"><path d="M12 8l6 6-6 6" stroke="#fff" stroke-width="3" fill="none"/></svg>
</section>

<section>
  <h2 class="abs welcome">WELCOME</h2>
  <p class="abs lead">Phasellus fringilla dictum velit, at consequat ligula porttitor sed consectetur elit eget aliquet auctor.</p>
  <p class="abs intro">Suspendisse fringilla ex ex, non commodo diam dictum eu. Nulla in euismod enim. Duis placerat, arcu vel tempor pulvinar, nisi erat egestas ante, in hendrerit diam tortor eu odio. Quisque blandit massa mi, in efficitur mi tristique id. Praesent et porta purus, in feugiat quam. Aenean non mattis elit. In molestie, leo nec consectetur bibendum, ex lectus accumsan ipsum, non porta nibh velit ut est. Nulla a augue velit. Suspendisse accumsan, dui eget tempor mattis, eros libero sodales lorem, eu ornare tellus ex eu erat. Pellentesque in vulputate massa. In sed arcu euismod, iaculis nunc ut, porta orci. Aenean luctus lorem quis nibh porttitor, vitae dictum est pretium.</p>
</section>

<section>
  <div class="abs card" style="left:131px;top:876px">
    <div class="photo" role="img" aria-label="Photo: gloved hands using a cryolipolysis applicator" style="background:linear-gradient(150deg,#9fd3e0,#e9eef0 55%,#5a7fd8)"></div>
    <div class="pill">CRYOLIPOLYSIS</div>
    <p class="text">Pellentesque in vulputate massa. In sed arcu euismod, iaculis nunc ut, porta orci. Aenean luctus lorem quis nibh porttitor, vitae dictum est pretium.</p>
    <a class="more">READ MORE</a>
  </div>
  <div class="abs card" style="left:451px;top:876px">
    <div class="photo" role="img" aria-label="Photo: body contouring treatment area marked with arrows" style="background:linear-gradient(180deg,#6cc2d6,#d8b9a4 45%,#8fd0de)"></div>
    <div class="pill">TRIMFLOX</div>
    <p class="text">Pellentesque in vulputate massa. In sed arcu euismod, iaculis nunc ut, porta orci. Aenean luctus lorem quis nibh porttitor, vitae dictum est pretium.</p>
    <a class="more">READ MORE</a>
  </div>
  <div class="abs card" style="left:770px;top:876px">
    <div class="photo" role="img" aria-label="Photo: shoulder and neck lymphatic massage" style="background:linear-gradient(135deg,#8ccfdc,#ecd2c2 50%,#b9a08c)"></div>
    <div class="pill">LYMFEMASSAGE</div>
    <p class="text">Pellentesque in vulputate massa. In sed arcu euismod, iaculis nunc ut, porta orci. Aenean luctus lorem quis nibh porttitor, vitae dictum est pretium.</p>
    <a class="more">READ MORE</a>
  </div>

  <div class="abs card" style="left:131px;top:1323px">
    <div class="photo" role="img" aria-label="Photo: back massage on a relaxed client" style="background:linear-gradient(150deg,#9cd6e2,#c99a7e 50%,#eaf3f5)"></div>
    <div class="pill">KORATHELIX</div>
    <p class="text">Pellentesque in vulputate massa. In sed arcu euismod, iaculis nunc ut, porta orci. Aenean luctus lorem quis nibh porttitor, vitae dictum est pretium.</p>
    <a class="more">READ MORE</a>
  </div>
  <div class="abs card" style="left:451px;top:1323px">
    <div class="photo" role="img" aria-label="Photo: calming head and face energy treatment" style="background:linear-gradient(160deg,#7ec8d8,#e8ccbb 50%,#6b5346)"></div>
    <div class="pill">AMBERLINE TIDE</div>
    <p class="text">Pellentesque in vulputate massa. In sed arcu euismod, iaculis nunc ut, porta orci. Aenean luctus lorem quis nibh porttitor, vitae dictum est pretium.</p>
    <a class="more">READ MORE</a>
  </div>
  <div class="abs card" style="left:770px;top:1323px">
    <div class="photo" role="img" aria-label="Photo: skincare bottles with green leaves and white flowers" style="background:linear-gradient(160deg,#5f7a6a,#c9cfc4 50%,#6f8a5e)"></div>
    <div class="pill">PRODUKTER</div>
    <p class="text">Pellentesque in vulputate massa. In sed arcu euismod, iaculis nunc ut, porta orci. Aenean luctus lorem quis nibh porttitor, vitae dictum est pretium.</p>
    <a class="more">READ MORE</a>
  </div>
</section>

<section>
  <div class="abs band"></div>
  <div class="abs tcard"></div>
  <h2 class="abs ttitle">TESTIMONIALS</h2>
  <svg class="abs" style="left:424px;top:1932px" width="16" height="24" viewBox="0 0 16 24"><path d="M12 2L3 12l9 10" stroke="#bbb" stroke-width="2" fill="none"/></svg>
  <div class="abs avatar" role="img" aria-label="Client portrait" style="left:465px"></div>
  <div class="abs avatar dark" role="img" aria-label="Client portrait" style="left:561px"></div>
  <div class="abs avatar" role="img" aria-label="Client portrait" style="left:656px"></div>
  <svg class="abs" style="left:760px;top:1932px" width="16" height="24" viewBox="0 0 16 24"><path d="M4 2l9 10-9 10" stroke="#bbb" stroke-width="2" fill="none"/></svg>
  <span class="abs qmark" style="left:188px">&#8220;</span>
  <p class="abs quote">Fusce condimentum, turpis ac placerat interdum, neque dolor viverra erat, id pulvinar ligula nulla eu urna. Vivamus vel molestie mi. Donec aliquam urna elit, vel molestie ipsum maximus rhoncus. Donec vitae neque et ex condimentum viverra tristique at metus. Curabitur sed consequat ipsum. Fusce eget tristique leo.</p>
  <span class="abs qmark" style="left:978px">&#8221;</span>
  <p class="abs author">Mira Holt, City</p>
</section>

<section>
  <h2 class="abs ctitle">CONTACT US</h2>
  <div class="abs field" style="left:131px;top:2248px;width:219px">Name</div>
  <div class="abs field" style="left:370px;top:2248px;width:219px">Email</div>
  <div class="abs field" style="left:609px;top:2248px;width:219px">Phone</div>
  <div class="abs field" style="left:848px;top:2248px;width:219px">Appointment for
    <svg style="position:absolute;right:12px;top:16px" width="9" height="9" viewBox="0 0 9 9"><path d="M1 3l3.5 3.5L8 3" stroke="#999" fill="none"/></svg>
  </div>
  <div class="abs field" style="left:131px;top:2306px;width:936px">Message</div>
  <div class="abs submit">SUBMIT</div>
</section>

<footer>
  <p class="abs flinks">Lirava &nbsp;| &nbsp;Behandlinger &nbsp;| &nbsp;Produkter &nbsp;| &nbsp;Priser &nbsp;| &nbsp;Kontakt</p>
  <p class="abs copy">Copyright © 2017 Company name. All rights reserved.</p>
  <div class="abs social" style="left:943px;background:#3b5998"></div>
  <div class="abs social" style="left:975px;background:#2aa3e0"></div>
  <div class="abs social" style="left:1008px;background:#0e76a8"></div>
  <div class="abs social" style="left:1041px;background:#dd4b39"></div>
</footer>

</body>
</html>
```